Card Design for my dog training business Brightpaw Obedience

Need a business card design for my dog training business with my new logo. Want the card to come off professional yet fun. Want it to be very eye catchy as well. I normally have these at vet clinics, pet stores, and groomers. so need it to look better than my competitors.
Target Market(s)
dog owners
Industry/Entity Type
Dog Training
Contact Information for Business Card
needs logo, my name and info
Font styles to use
Serif
Colors
0255a3
ffffff
ec1f27
000000
333333
fbfbfb
Requirements
Must have
- Brightpaw Obedience
- Felix Orland
- 415 903 2276
- info@brightpawobedience.example
- www.brightpawobedience.example

```html
<!DOCTYPE html>
<html lang="en">
<head>
<meta charset="utf-8">
<title>Brightpaw Obedience – Business Card</title>
<link rel="stylesheet" href="https://fonts.googleapis.com/css2?family=EB+Garamond:ital,wght@0,500;1,400&family=Montserrat:wght@400;600&display=swap">
<style>
  :root {
    --brand-blue: #16437e;
    --accent-blue: #0255a3;
    --charcoal: #2a2b2d;
    --ink: #1c1c1c;
    --paper: #fbfbfb;
    --stage: #d9d9d9;
    --muted: #333333;
  }
  * { box-sizing: border-box; margin: 0; padding: 0; }
  html, body { width: 1200px; height: 869px; overflow: hidden; }
  body { background: var(--stage); font-family: "Montserrat", sans-serif; position: relative; }

  .card {
    position: absolute;
    width: 560px;
    height: 320px;
    overflow: hidden;
    box-shadow: 0 10px 24px rgba(0,0,0,0.25);
  }

  /* Front: identity side */
  .card-front { left: 70px; top: 110px; background: var(--paper); }
  .brand-lockup {
    position: absolute; left: 44px; top: 46px;
    display: flex; align-items: center; gap: 10px;
  }
  .brand-lockup .brand-square { width: 14px; height: 14px; background: var(--ink); }
  .brand-lockup .brand-name {
    font-family: "EB Garamond", serif; font-weight: 500;
    font-size: 22px; color: var(--ink); letter-spacing: 0.5px;
  }
  .holder-name {
    position: absolute; right: 44px; top: 110px;
    font-weight: 600; font-size: 19px; letter-spacing: 1.5px;
    color: var(--ink); text-transform: uppercase;
  }
  .contact-list {
    position: absolute; left: 44px; top: 196px;
    list-style: none; display: flex; flex-direction: column; gap: 6px;
  }
  .contact-list li {
    display: flex; align-items: center; gap: 12px;
    font-size: 12.5px; color: var(--muted); letter-spacing: 0.3px;
  }
  .contact-list svg { width: 12px; height: 12px; fill: var(--accent-blue); flex: none; }
  .tagline {
    position: absolute; left: 40px; top: 268px;
    font-family: "EB Garamond", serif; font-style: italic;
    font-size: 23px; color: var(--accent-blue); white-space: nowrap;
  }

  /* Back: brand side */
  .card-back { left: 570px; top: 440px; background: var(--charcoal); }
  .card-back .blue-field {
    position: absolute; left: 0; top: 0; bottom: 0; width: 44%;
    background: var(--brand-blue);
  }
  .card-back .brand-lockup-large {
    position: absolute; inset: 0;
    display: flex; align-items: center; justify-content: center; gap: 16px;
  }
  .brand-lockup-large .brand-square { width: 22px; height: 22px; background: var(--paper); }
  .brand-lockup-large .brand-name {
    font-family: "EB Garamond", serif; font-weight: 500;
    font-size: 40px; color: var(--paper); letter-spacing: 1px;
  }
</style>
</head>
<body>

<section class="card card-front" aria-label="Business card front">
  <div class="brand-lockup">
    <span class="brand-square"></span>
    <span class="brand-name">Brightpaw Obedience</span>
  </div>

  <h1 class="holder-name">Felix Orland</h1>

  <ul class="contact-list">
    <li>
      <svg viewBox="0 0 24 24" aria-hidden="true"><path d="M6.6 10.8a15.1 15.1 0 0 0 6.6 6.6l2.2-2.2c.3-.3.7-.4 1-.2 1.1.4 2.3.6 3.6.6.6 0 1 .4 1 1V20c0 .6-.4 1-1 1A17 17 0 0 1 3 4c0-.6.4-1 1-1h3.5c.6 0 1 .4 1 1 0 1.3.2 2.5.6 3.6.1.3 0 .7-.2 1z"/></svg>
      415 903 2276
    </li>
    <li>
      <svg viewBox="0 0 24 24" aria-hidden="true"><path d="M2 5h20v14H2zm2 2v.5l8 5 8-5V7zm0 2.8V17h16V9.8l-8 5z"/></svg>
      info@brightpawobedience.example
    </li>
    <li>
      <svg viewBox="0 0 24 24" aria-hidden="true"><circle cx="12" cy="12" r="10"/></svg>
      www.brightpawobedience.example
    </li>
  </ul>

  <p class="tagline">“Patient, positive lessons for every dog in town.”</p>
</section>

<section class="card card-back" aria-label="Business card back">
  <div class="blue-field"></div>
  <div class="brand-lockup-large">
    <span class="brand-square"></span>
    <span class="brand-name">Brightpaw Obedience</span>
  </div>
</section>

</body>
</html>
```